Residential Remodeling Contractor needs updated business card

I need a new design for my business card.
Name of the company is Ridgefell Construction. I need a card that commands presence, strength, integrity. I have been in business for 28 years. I am a Residential Remodeling Contractor that covers all aspects of a residential remodel and build.

```html
<!DOCTYPE html>
<html lang="en">
<head>
<meta charset="utf-8">
<title>Ridgefell Construction – Business Card</title>
<link rel="stylesheet" href="https://fonts.googleapis.com/css2?family=Cinzel:wght@600&family=Montserrat:wght@400;600&display=swap">
<style>
  :root {
    --backdrop: #2b2521;
    --card-blue: #1f3c80;
    --ink-white: #ffffff;
    --beam-soft: rgba(255, 255, 255, 0.7);
    --beam-fade: rgba(255, 255, 255, 0);
  }
  * { margin: 0; padding: 0; box-sizing: border-box; }
  html, body {
    width: 1200px; height: 786px; overflow: hidden;
    background: var(--backdrop);
    font-family: "Montserrat", sans-serif;
  }
  .canvas {
    position: relative; width: 1200px; height: 786px;
    display: flex; align-items: center; justify-content: center; gap: 40px;
  }
  .card {
    position: relative; width: 540px; height: 309px;
    background: var(--card-blue); color: var(--ink-white);
    overflow: hidden; box-shadow: 0 10px 28px rgba(0,0,0,0.45);
  }
  .wordmark {
    position: absolute; font-family: "Cinzel", serif; font-weight: 600;
    letter-spacing: 0.02em; line-height: 1.1; color: var(--ink-white);
    white-space: nowrap;
  }
  .wordmark span { display: block; }

  /* Contact side */
  .card--contact .wordmark { left: 30px; top: 112px; font-size: 28px; }
  .card--contact .wordmark span + span { padding-left: 14px; }
  .holder { position: absolute; right: 110px; top: 26px; text-align: right; }
  .holder__name { font-weight: 600; font-size: 16px; }
  .holder__role { font-size: 9px; margin-top: 1px; }
  .contact-illustration {
    position: absolute; left: 300px; top: 100px; width: 240px; height: 209px;
    background: linear-gradient(90deg, var(--beam-fade) 0%, var(--beam-soft) 60%, var(--ink-white) 85%);
  }
  .address { position: absolute; left: 30px; top: 206px; font-size: 10.5px; line-height: 1.3; }
  .contact-list { position: absolute; left: 30px; top: 240px; list-style: none; font-size: 10.5px; }
  .contact-list li { display: flex; align-items: center; gap: 9px; height: 19px; }
  .contact-list svg { width: 12px; height: 12px; fill: var(--ink-white); flex: none; }

  /* Brand side */
  .brand-illustration {
    position: absolute; left: 0; top: 0; width: 240px; height: 309px;
    background: linear-gradient(20deg, var(--ink-white) 0%, var(--ink-white) 35%, var(--beam-soft) 55%, var(--beam-fade) 100%);
  }
  .card--brand .wordmark { left: 265px; top: 118px; font-size: 28px; }
  .card--brand .wordmark span + span { padding-left: 16px; }
</style>
</head>
<body>
<main class="canvas">
  <section class="card card--contact" aria-label="Business card, contact side">
    <div class="contact-illustration" role="img" aria-label="Lighthouse illustration casting a light beam to the left"></div>
    <div class="holder">
      <p class="holder__name">Daniel Harlow</p>
      <p class="holder__role">Owner</p>
    </div>
    <h1 class="wordmark"><span>Ridgefell</span><span>Construction</span></h1>
    <p class="address">240 Cedar Bend Road<br>Brandon, MS 39042</p>
    <ul class="contact-list">
      <li><svg viewBox="0 0 24 24" aria-hidden="true"><path d="M6.6 10.8a15.1 15.1 0 0 0 6.6 6.6l2.2-2.2a1 1 0 0 1 1-.25 11.4 11.4 0 0 0 3.6.57 1 1 0 0 1 1 1V20a1 1 0 0 1-1 1A17 17 0 0 1 3 4a1 1 0 0 1 1-1h3.5a1 1 0 0 1 1 1c0 1.25.2 2.45.57 3.57a1 1 0 0 1-.25 1z"/></svg>555.014.2297</li>
      <li><svg viewBox="0 0 24 24" aria-hidden="true"><path d="M2 5h20v14H2z M2 5l10 8 10-8" fill="none" stroke="#fff" stroke-width="2"/></svg>info@ridgefellconstruction.com</li>
      <li><svg viewBox="0 0 24 24" aria-hidden="true"><circle cx="12" cy="12" r="10"/></svg>www.ridgefellconstruction.com</li>
    </ul>
  </section>

  <section class="card card--brand" aria-label="Business card, brand side">
    <div class="brand-illustration" role="img" aria-label="Large lighthouse illustration with a light beam sweeping to the upper right"></div>
    <h2 class="wordmark"><span>Ridgefell</span><span>Construction</span></h2>
  </section>
</main>
</body>
</html>
```